Etikett für Likörflasche - Tinderbox
Zielgruppe
Wir sind eine kleine Tinderbox / Likörmanufaktur. Unser Obst für die Brände und Liköre stammt aus eigenem Anbau bzw. von umliegenden regionalen Bauern. Hier setzen wir auf sehr gute Qualität und verwenden keine Zusatzstoffe, Geschmacksverstärker, Farbstoffe etc. Im ersten Schritt werden wir nur 3-4 verschiedene Liköre anbieten.
Wir möchten unsere Liköre zukünftig auf Veranstaltungen / Events und Märkten verkaufen. Hierfür suchen wir ein pfiffiges und ansprechendes Etikettendesign.
Das Wort 'Tinderbox' soll die Leute auf den Events zu uns führen. Das wird auch mit großen Fahnen am Verkaufsstand beworben. Da wir auch ein paar amerikanische Foodtrucks haben soll auch das Etikett ein bisschen amerikanisch gehalten werden.
Zielgruppe: 28 bis 55 Jahre (Männer & Frauen)
Verkaufspreis pro 0,5 Liter Flasche ca. 24,50 Euro
Aufgabenstellung
Es soll ein Etikett auf die Flasche (nur vorne nicht auf die Rückseite).
Etikettengröße: ca. 7,0 x 8,5cm (für die 0,5l Flasche)
Angaben die sich auf dem Etikett ändern:
- Inhalt entweder 0,35l oder 0,5l Flasche
- Bezeichnung vom Inhalt und 'Kurzbeschreibung'
- Alkoholgehalt
Ich habe in PowerPoint schon mal ein Etikett zusammen gestellt, auf dem die Angaben alle mit enthalten sind. Hier fehlt mir allerdings der Pfiff und das Professionelle. Auch die Darstellung der Eigenschaften wie 'Echte Früchte', 'Handcrafted' etc. gefällt mir so auch nicht. Vielleicht wäre auch noch ein cooler Spruch darauf gut.
In die Anlage habe ich meine kreierte PowerPoint Folie gepackt (auf der 2. Folie findet ihr die geplante Flasche in die abgefüllt wird). Die zweite Datei ist ein Design was meinen Vorstellungen schon gut nahe kommt aus dem Internet (hier gefallen mir die Linien, kleine Gimmicks etc. da passiert einfach was auf dem Etikett). Von der Art her würde mir dieser Style gut gefallen. Es soll nur nicht zu überladen und kitschig werden.
Likörsorten die es geben wird: Wir werden uns erstmal auf 3-4 Sorten beschränken.

```html
<!DOCTYPE html>
<html lang="de">
<head>
<meta charset="utf-8">
<title>Baron Tinderbox – Brombeer Reserve Etikett</title>
<link href="https://fonts.googleapis.com/css2?family=Alegreya+Sans+SC:wght@700;800&family=Oswald:wght@600&family=Playfair+Display:wght@400;700;900&display=swap" rel="stylesheet">
<style>
  :root {
    --page: #ffffff;
    --paper-light: #f4f3f1;
    --paper-mid: #e6e5e2;
    --ink: #1c1a1a;
    --red: #c8202a;
    --rule: #6d6d6d;
    --art-grey: #cfcfcd;
  }
  * { margin: 0; padding: 0; box-sizing: border-box; }
  html, body {
    width: 1200px; height: 953px; overflow: hidden;
    background: var(--page);
  }
  .canvas { position: relative; width: 1200px; height: 953px; }
  .label {
    position: absolute; left: 321px; top: 136px;
    width: 558px; height: 675px;
    border-radius: 12px;
    background: radial-gradient(ellipse at 50% 45%, var(--paper-light) 0%, var(--paper-mid) 100%);
    box-shadow: 0 0 14px rgba(0,0,0,0.12);
    overflow: hidden;
    color: var(--ink);
    text-align: center;
  }
  .label > * { position: absolute; left: 0; right: 0; }
  .backdrop-art { top: 40px; left: 40px; right: auto; width: 477px; height: 460px; }
  .origin-line {
    top: 150px;
    font: 600 26px/1 "Oswald", sans-serif;
    letter-spacing: 5px;
  }
  .brand-name {
    top: 188px;
    font: 900 70px/0.95 "Playfair Display", serif;
    color: var(--ink);
  }
  .star-rule { top: 322px; height: 20px; }
  .product-name {
    top: 350px;
    font: 400 52px/1 "Playfair Display", serif;
    color: var(--red);
  }
  .description {
    top: 414px;
    font: 700 27px/36px "Playfair Display", serif;
    letter-spacing: -0.4px;
  }
  .spec-rule { height: 2px; background: var(--rule); }
  .spec-rule.top-left { top: 515px; left: 75px; right: auto; width: 130px; }
  .spec-rule.top-right { top: 515px; left: 357px; right: auto; width: 130px; }
  .spec-rule.bottom { top: 565px; left: 75px; right: auto; width: 412px; }
  .specs {
    top: 522px;
    font: 800 30px/1.2 "Alegreya Sans SC", sans-serif;
    letter-spacing: 1px;
  }
  .specs .sep { font-size: 16px; vertical-align: 4px; margin: 0 3px; }
  .claim {
    top: 576px;
    font: 800 25px/1.2 "Alegreya Sans SC", sans-serif;
    color: var(--red);
    letter-spacing: 1px;
  }
  .address {
    top: 606px;
    font: 700 19px/1.2 "Alegreya Sans SC", sans-serif;
    letter-spacing: 0.2px;
  }
  .web {
    top: 629px;
    font: 700 15.5px/1.2 "Alegreya Sans SC", sans-serif;
    letter-spacing: 0.5px;
  }
</style>
</head>
<body>
<div class="canvas">
  <div class="label">
    <svg class="backdrop-art" viewBox="0 0 477 460" role="img" aria-label="Faint grey hand-drawn illustration of a fruit with leaf and sunburst rays behind the lettering">
      <defs>
        <radialGradient id="artFade" cx="50%" cy="55%" r="50%">
          <stop offset="0%" stop-color="var(--art-grey)" stop-opacity="0.55"/>
          <stop offset="100%" stop-color="var(--art-grey)" stop-opacity="0"/>
        </radialGradient>
      </defs>
      <rect width="477" height="460" fill="url(#artFade)"/>
    </svg>

    <div class="origin-line">AUS EIGENEM ANBAU</div>
    <div class="brand-name">Baron<br>Tinderbox</div>

    <svg class="star-rule" viewBox="0 0 558 20" aria-hidden="true">
      <line x1="149" y1="10" x2="226" y2="10" stroke="var(--rule)" stroke-width="2"/>
      <line x1="331" y1="10" x2="406" y2="10" stroke="var(--rule)" stroke-width="2"/>
      <polygon points="242,2 244.4,7.6 250.5,8.1 245.9,12.1 247.3,18 242,14.8 236.7,18 238.1,12.1 233.5,8.1 239.6,7.6" fill="var(--rule)"/>
      <polygon points="278,1 280.6,7.2 287.3,7.7 282.2,12.1 283.8,18.5 278,15 272.2,18.5 273.8,12.1 268.7,7.7 275.4,7.2" fill="var(--rule)"/>
      <polygon points="314,2 316.4,7.6 322.5,8.1 317.9,12.1 319.3,18 314,14.8 308.7,18 310.1,12.1 305.5,8.1 311.6,7.6" fill="var(--rule)"/>
    </svg>

    <div class="product-name">Brombeer Reserve</div>
    <p class="description">Wilde Beeren treffen auf vielschichtige<br>Noten von Whiskey und Karamell</p>

    <div class="spec-rule top-left"></div>
    <div class="spec-rule top-right"></div>
    <div class="specs">500ml<span class="sep">✦</span>22% Vol<span class="sep">✦</span>44 Proof</div>
    <div class="spec-rule bottom"></div>

    <div class="claim">Seasoned Fruits Complete Handcrafted</div>
    <div class="address">Baron's Tinderbox – Am Lindenhang 12 – 91244 Feldkirchen</div>
    <div class="web">WWW.BARONS-TINDERBOX.DE</div>
  </div>
</div>
</body>
</html>
```